Real Estate Business Card

On the front side I want to have my info, my brokerage info.
On the back side I want have my complany’s logo, website and Facebook link. I will provide all this once I select a design.

I would like to see Black background and gold text, Dark Blue and gold text and White and blue text designs

Font styles to use
Sans Serif
Script

```html
<!DOCTYPE html>
<html lang="en">
<head>
<meta charset="utf-8">
<title>HARBORKEY Realty – Business Card</title>
<link rel="stylesheet" href="https://fonts.googleapis.com/css2?family=Cabin:wght@400;600;700&display=swap">
<style>
  :root {
    --backdrop: #8a9bab;
    --navy: #020a1f;
    --gold: #e6c04a;
    --gold-light: #f6dc82;
    --gold-deep: #b8862c;
  }
  * { margin: 0; padding: 0; box-sizing: border-box; }
  html, body { width: 1200px; height: 462px; overflow: hidden; }
  body {
    background: var(--backdrop);
    font-family: "Cabin", Arial, sans-serif;
    color: var(--gold);
    position: relative;
  }
  .card {
    position: absolute;
    background: var(--navy);
    box-shadow: 0 6px 18px rgba(0, 0, 0, 0.35);
  }
  /* Front side */
  .card-front { left: 162px; top: 106px; width: 438px; height: 250px; }
  .brand {
    position: absolute;
    display: flex; flex-direction: column; align-items: center;
    text-align: center;
  }
  .brand-mark { background: var(--gold); }
  .brand-name { font-weight: 700; color: var(--gold); letter-spacing: 0.04em; line-height: 1.05; }
  .card-front .brand { left: 21px; top: 90px; width: 160px; }
  .card-front .brand-mark { width: 30px; height: 30px; margin-bottom: 8px; }
  .card-front .brand-name { font-size: 17px; }
  .divider {
    position: absolute; left: 211px; top: 42px;
    width: 2px; height: 166px;
    background: linear-gradient(180deg, var(--gold-light), var(--gold-deep));
  }
  .contact { position: absolute; right: 66px; text-align: right; font-size: 8.5px; line-height: 1.3; }
  .contact-name { top: 78px; }
  .contact-name .name { font-size: 10px; font-weight: 600; }
  .contact-name .role { font-size: 5.5px; letter-spacing: 0.08em; font-weight: 600; }
  .contact-phone { top: 112px; }
  .contact-email { top: 143px; }
  .contact-address { top: 164px; }
  .icon { position: absolute; left: 378px; width: 14px; height: 14px; }
  .icon-phone { top: 115px; }
  .icon-email { top: 144px; }
  .icon-pin { top: 166px; }
  /* Back side */
  .card-back { left: 643px; top: 110px; width: 426px; height: 244px; }
  .foil-band {
    position: absolute; top: 8px; width: 11px; height: 228px;
    background: linear-gradient(90deg, var(--gold-deep), var(--gold-light) 45%, var(--gold) 70%, var(--gold-deep));
  }
  .foil-left { left: 0; border-radius: 0 6px 6px 0; }
  .foil-right { right: 0; border-radius: 6px 0 0 6px; }
  .card-back .brand { left: 88px; top: 72px; width: 250px; }
  .card-back .brand-mark { width: 46px; height: 46px; margin-bottom: 12px; }
  .card-back .brand-name { font-size: 26px; }
  .links {
    position: absolute; left: 110px; top: 218px;
    display: flex; gap: 18px; font-size: 7.5px; align-items: center;
  }
  .link { display: flex; align-items: center; gap: 8px; }
  .link-icon { width: 16px; height: 16px; }
  .social-dot { width: 14px; height: 14px; border-radius: 50%; background: var(--gold-deep); }
</style>
</head>
<body>
  <section class="card card-front" aria-label="Card front">
    <div class="brand">
      <div class="brand-mark"></div>
      <div class="brand-name">HARBORKEY REALTY</div>
    </div>
    <div class="divider"></div>

    <div class="contact contact-name">
      <div class="name">Jordan Hale</div>
      <div class="role">BROKER</div>
    </div>
    <div class="contact contact-phone">+43298765432<br>+41255501234</div>
    <div class="contact contact-email">jordan.hale@harborkey.com</div>
    <div class="contact contact-address">Oak Lane 8,<br>TOWN<br>5678 CA</div>

    <svg class="icon icon-phone" viewBox="0 0 24 24" aria-hidden="true">
      <path fill="var(--gold)" d="M6.6 10.8a15 15 0 0 0 6.6 6.6l2.2-2.2a1 1 0 0 1 1-.25 11.4 11.4 0 0 0 3.6.57 1 1 0 0 1 1 1V20a1 1 0 0 1-1 1A17 17 0 0 1 3 4a1 1 0 0 1 1-1h3.5a1 1 0 0 1 1 1c0 1.25.2 2.45.57 3.6a1 1 0 0 1-.25 1z"/>
    </svg>
    <svg class="icon icon-email" viewBox="0 0 24 24" aria-hidden="true">
      <rect x="2" y="5" width="20" height="14" fill="none" stroke="var(--gold)" stroke-width="1.6"/>
      <path d="M2 5l10 8 10-8M2 19l7-7M22 19l-7-7" fill="none" stroke="var(--gold)" stroke-width="1.6"/>
    </svg>
    <svg class="icon icon-pin" viewBox="0 0 24 24" aria-hidden="true">
      <path fill="var(--gold)" d="M12 2a7 7 0 0 0-7 7c0 5 7 13 7 13s7-8 7-13a7 7 0 0 0-7-7zm0 9.5A2.5 2.5 0 1 1 12 6.5a2.5 2.5 0 0 1 0 5z"/>
    </svg>
  </section>

  <section class="card card-back" aria-label="Card back">
    <div class="foil-band foil-left"></div>
    <div class="foil-band foil-right"></div>
    <div class="brand">
      <div class="brand-mark"></div>
      <div class="brand-name">HARBORKEY REALTY</div>
    </div>
    <div class="links">
      <div class="link">
        <svg class="link-icon" viewBox="0 0 24 24" aria-hidden="true">
          <g fill="none" stroke="var(--gold-deep)" stroke-width="1.6">
            <circle cx="12" cy="12" r="9"/>
            <ellipse cx="12" cy="12" rx="4" ry="9"/>
            <path d="M3 12h18M5 7h14M5 17h14"/>
          </g>
        </svg>
        <span>www.harborkey.com</span>
      </div>
      <div class="link">
        <div class="social-dot"></div>
        <span>www.social.com/harborkey</span>
      </div>
    </div>
  </section>
</body>
</html>
```